Home Staging Company needs business card design

We're a home staging company called Brightly Settled Home Staging. We would like a business card design that includes aqua and gray. Our current logo of house within chair is fine but I find we almost always use the logo in one color. I'll upload images of front and back of our current card and our logo. Note that we have dropped "Solutions" from our company name and don't want to include it on the card.

Target Market(s)

Realtors and homeowners - people interested in selling their homes

Contact Information for Business Card

Marisol Thistlewood
Brightly Settled Home Staging
757-555-0193
www.brightlysettled.com
marisol@brightlysettled.com

Font styles to use
Serif
Script

Requirements
Must have
• My logo and contact details
• UPDATE***
• I forgot to say that the company name should be included on the front of the card somehow.

```html
<!DOCTYPE html>
<html lang="en">
<head>
<meta charset="utf-8">
<title>Brightly Settled Home Staging – Business Card</title>
<link href="https://fonts.googleapis.com/css2?family=Playfair+Display:wght@700&family=Questrial&display=swap" rel="stylesheet">
<style>
  :root {
    --backdrop: #3b3b3c;
    --card: #1d1d1e;
    --card-edge: #141415;
    --aqua: #4fb8c9;
    --white: #f4f4f4;
    --muted: #cfcfcf;
    --gloss: #4a4a4c;
    --faint: #2a2a2c;
  }
  * { margin: 0; padding: 0; box-sizing: border-box; }
  html, body { width: 799px; height: 1200px; overflow: hidden; }
  body {
    background: var(--backdrop);
    font-family: "Questrial", sans-serif;
    position: relative;
  }
  .card {
    position: absolute;
    left: 80px;
    width: 640px;
    height: 366px;
    background: var(--card);
    border: 1px solid var(--card-edge);
    overflow: hidden;
  }
  .card--front { top: 110px; }
  .card--back { top: 720px; }

  /* Front */
  .front-mark {
    position: absolute;
    inset: 0;
    display: flex;
    align-items: center;
    justify-content: center;
    gap: 18px;
  }
  .front-mark .dot {
    width: 34px; height: 34px; border-radius: 50%;
    background: var(--gloss);
  }
  .front-mark .brand {
    font-family: "Playfair Display", serif;
    font-weight: 700;
    font-size: 30px;
    color: var(--gloss);
    line-height: 1.15;
  }

  /* Back */
  .edge-tab {
    position: absolute;
    left: -22px; top: 34px;
    width: 44px; height: 44px;
    border-radius: 50%;
    background: var(--aqua);
  }
  .identity { position: absolute; left: 42px; top: 36px; }
  .identity .name {
    font-size: 21px;
    color: var(--white);
    letter-spacing: 0.3px;
  }
  .identity .name .surname { color: var(--aqua); }
  .identity .role {
    font-size: 12px;
    color: var(--muted);
    margin-top: 4px;
  }
  .contacts {
    position: absolute;
    left: 30px; top: 210px;
    list-style: none;
  }
  .contacts li {
    display: flex; align-items: center; gap: 14px;
    font-size: 15px;
    color: var(--white);
    height: 24px;
  }
  .contacts svg { width: 14px; height: 14px; fill: var(--aqua); flex: none; }
  .back-brand {
    position: absolute;
    left: 300px; top: 124px;
    display: flex; align-items: center; gap: 12px;
  }
  .back-brand .dot {
    width: 40px; height: 40px; border-radius: 50%;
    background: var(--aqua);
    flex: none;
  }
  .back-brand .brand {
    font-family: "Playfair Display", serif;
    font-weight: 700;
    font-size: 23px;
    color: var(--white);
    line-height: 1.15;
  }
  .faint-circle {
    position: absolute;
    left: 330px; top: 235px;
    width: 190px; height: 190px;
    border-radius: 50%;
    background: var(--faint);
  }
</style>
</head>
<body>

<section class="card card--front" aria-label="Card front">
  <div class="front-mark">
    <span class="dot"></span>
    <span class="brand">Brightly Settled<br>Home Staging</span>
  </div>
</section>

<section class="card card--back" aria-label="Card back">
  <span class="faint-circle"></span>
  <span class="edge-tab"></span>

  <div class="identity">
    <p class="name">Marisol <span class="surname">Thistlewood</span></p>
    <p class="role">Managing Director</p>
  </div>

  <div class="back-brand">
    <span class="dot"></span>
    <span class="brand">Brightly Settled<br>Home Staging</span>
  </div>

  <ul class="contacts">
    <li>
      <svg viewBox="0 0 24 24" aria-hidden="true"><path d="M6.6 10.8a15.1 15.1 0 0 0 6.6 6.6l2.2-2.2a1 1 0 0 1 1-.25 11.4 11.4 0 0 0 3.6.57 1 1 0 0 1 1 1V20a1 1 0 0 1-1 1A17 17 0 0 1 3 4a1 1 0 0 1 1-1h3.5a1 1 0 0 1 1 1c0 1.25.2 2.45.57 3.6a1 1 0 0 1-.25 1z"/></svg>
      757-555-0193
    </li>
    <li>
      <svg viewBox="0 0 24 24" aria-hidden="true"><path d="M12 2a10 10 0 1 0 0 20 10 10 0 0 0 0-20zm6.9 6h-2.9a15.6 15.6 0 0 0-1.4-3.6A8 8 0 0 1 18.9 8zM12 4a14 14 0 0 1 1.9 4h-3.8A14 14 0 0 1 12 4zM4.3 14a8.2 8.2 0 0 1 0-4h3.4a16.5 16.5 0 0 0 0 4zm.8 2h2.9a15.6 15.6 0 0 0 1.4 3.6A8 8 0 0 1 5.1 16zM8 8H5.1a8 8 0 0 1 4.3-3.6A15.6 15.6 0 0 0 8 8zm4 12a14 14 0 0 1-1.9-4h3.8A14 14 0 0 1 12 20zm2.3-6H9.7a14.7 14.7 0 0 1 0-4h4.6a14.7 14.7 0 0 1 0 4zm.3 5.6A15.6 15.6 0 0 0 16 16h2.9a8 8 0 0 1-4.3 3.6zM16.3 14a16.5 16.5 0 0 0 0-4h3.4a8.2 8.2 0 0 1 0 4z"/></svg>
      www.brightlysettled.com
    </li>
    <li>
      <svg viewBox="0 0 24 24" aria-hidden="true"><path d="M3 5h18a1 1 0 0 1 1 1v12a1 1 0 0 1-1 1H3a1 1 0 0 1-1-1V6a1 1 0 0 1 1-1zm1 2.2V17h16V7.2l-8 5.3z M4.6 7 12 11.9 19.4 7z"/></svg>
      marisol@brightlysettled.com
    </li>
  </ul>
</section>

</body>
</html>
```